Northway Value Bureau (Account) WP Design

We need an Account (Profile) Wordpress design to add to nvb.co.uk.

The design should be based on https://nvb.co.uk/about/. The look and feel of the menu on the left.

The logic, after login the header menu will add another page:

Before Login:
Home / About / Trading / Support /

After Login
Home / About / Trading / Support / Account (Demo) - Logout

When you click on the / Account /

"Account Profile" page is loaded where you can change the settings etc.

"Account Profile" menu on the left should look the same as in / About / (https://nvb.co.uk/about/)

We need the following sub-pages under "Account Profile"

- Profile
- Transfers
- Reports
- Security
- API Key
- Affiliates

Now looking into each page:
-
- Profile (Should be split into individual or business) a user can choose whether how he want to run his account:

[Individual]

Personal Details
First Name:
Middle Name:
Family Name:
Citizenship:
Gender:
DOB:

[Attach File] (Government Issues ID, Passport, Driving License) - Verify

Contact Information
Phone: +44 207 555 0143 - Verify
E-Mail: sample@mailbox.example - Verify

Residential Address
Address line 1:
Address line 2:
Address line 3:
City:
Postcode:
Country:

[Attach File] (Utility Bill or Bank Statement) - Verify

[Business]

Company Name:
Registration Number:

Registered Address
Address line 1:
Address line 2:
Address line 3:
City:
Postcode:
Country:

[Attach File] (Certificate of Incorporation) - Verify
[Attach File] (Memorandum & Articles of Association)
[Attach File] (Shareholder Register)

Company Contact Information
Website:

-

- Transfers (Where a user can link a bank account to deposit or withdraw funds from the account)

Transfers

Add a bank account:

Please select the country where beneficiary’s bank is domicile: [Please select]
Please select the currency you wish to make transfers in: [Please select]

Full beneficiary name:
Full beneficiary address:
Beneficiary bank name:
Beneficiary bank address:
Beneficiary Bank Identification Code (BIC)/Routing Code:
Beneficiary IBAN number/account number:

[SAVE]

Deposti funds to NVB Bank Account
Amount of currency to be received e.g. 2345.67 [Please select: USD, EUR, GBP] :
Full beneficiary name: Northway Value Bureau Limited
Full beneficiary address: Kestrel Court
7-9 Fenwick Row
London, United Kingdom
Beneficiary bank name:
Beneficiary bank address:
Beneficiary Bank Identification Code (BIC)/Routing Code: XXXXXXXXXX
Beneficiary IBAN number/account number: XXXXXXXXXXXXXXXXXXXXXXXXXX

Deposit coins to NVB Coin Account
Amount of coins to be received e.g. 2345.67 [Please select: BTC, LTC]:
NVB Coin Account: XXXXXXXXXXXXXXXXXXXXXXXXXXXXX

Applicable charges (?):
[Clear] [Continue]

Withdraw funds from NVB Bank Account
Amount of currency to be sent e.g. 2345.67 [Please select: USD, EUR, GBP] :

Withdraw coins from NVB Coin Account:
Amount of coins to be sent e.g. 2345.67 [Please select: BTC, LTC]:
Please specify you coin account: XXXXXXXXXXXXXXXXXXXXXXXXXXXXX

Applicable charges (?):
[Clear] [Continue]

-

- Reports

TBC
-

- Security

Change Password
Current Password:
New Password:
Confirm New Password:

Enable / Disable : Two-factor Authentication (SMS)

-

- API Key
TBC

-
- Affiliates

Unlimited earning potential!
You'll receive up to 10% commission on all trades made through your affiliate link.

Referral Circle Scheme
Simply apply to our program from your publisher account or click the "Join Now" button below.

Corvalent.com - Join Now

```html
<!DOCTYPE html>
<html lang="en">
<head>
<meta charset="utf-8">
<title>Northway Value Bureau – Account Profile</title>
<link href="https://fonts.googleapis.com/css2?family=Arimo:wght@400;700&display=swap" rel="stylesheet">
<style>
  :root{
    --backdrop:#333333;
    --page:#ffffff;
    --brand:#009ad3;
    --brand-light:#2eaee0;
    --title-band:#e4e4e4;
    --ink:#111111;
    --ink-soft:#555555;
    --rule:#333333;
    --field-border:#b8b8b8;
    --button-dark:#444444;
  }
  *{box-sizing:border-box;margin:0;padding:0}
  html,body{width:1200px;height:839px;overflow:hidden;background:var(--backdrop)}
  body{font-family:"Arimo",Arial,sans-serif}
  .stage{position:relative;width:1348px;height:942px;transform:scale(0.89021);transform-origin:0 0;background:var(--backdrop)}
  .page{position:absolute;left:74px;top:0;width:1200px;height:903px;background:var(--page)}
  .abs{position:absolute}

  /* header */
  .brand-name{left:111px;top:20px;width:160px;font-size:12px;letter-spacing:6px;line-height:22px;color:#444;text-transform:uppercase}
  .brand-divider{left:272px;top:14px;width:1px;height:64px;background:#999}
  .brand-dot{left:286px;top:26px;width:14px;height:14px;border-radius:50%;background:var(--brand)}
  .main-nav{left:286px;top:66px;font-size:12px;color:var(--ink-soft)}
  .login-field{top:41px;width:131px;height:24px;border:1px solid var(--field-border);font-size:12px;color:#999;padding:4px 5px;background:#fff}
  .login-field .hint{position:absolute;right:12px;top:3px;width:17px;height:17px;border:1px solid #bbb;border-radius:50%;font-size:11px;text-align:center;line-height:15px;color:#bbb}
  .btn{top:40px;height:24px;width:55px;border-radius:3px;color:#fff;font-size:11px;text-align:center;line-height:24px}
  .btn-login{left:974px;background:var(--button-dark)}
  .btn-signup{left:1034px;background:var(--brand)}

  /* ticker */
  .ticker{left:0;top:102px;width:1200px;height:49px;background:var(--brand);color:#fff}
  .coin-mark{left:239px;top:9px;width:30px;height:30px;border-radius:50%;border:2px solid #fff}
  .tick{top:8px;font-size:11px;line-height:14px}
  .tick b{display:block;font-weight:400;font-size:14px;margin-top:3px}
  .tick small{font-size:10px}
  .tick-rule{top:0;width:1px;height:49px;background:var(--brand-light)}

  /* title band */
  .title-band{left:0;top:151px;width:1200px;height:78px;background:var(--title-band);border-bottom:1px solid #ccc}
  .page-title{left:126px;top:21px;font-size:30px;font-weight:700;color:var(--ink)}

  /* side menu */
  .side-menu{left:126px;top:262px;width:217px;list-style:none}
  .side-menu li{height:38px;font-size:16px;color:var(--ink);border-bottom:1px solid var(--rule);line-height:36px;position:relative}
  .side-menu li:last-child{border-bottom:none}
  .side-menu .expand{position:absolute;right:2px;top:11px;width:15px;height:15px;background:#999;color:#fff;font-size:14px;line-height:14px;text-align:center}

  /* security form */
  .section-title{left:399px;top:270px;font-size:30px;font-weight:700;color:var(--ink-soft)}
  .form-heading{left:437px;top:332px;font-size:15px;font-weight:700;color:var(--ink)}
  .field-label{width:300px;left:267px;text-align:right;font-size:15px;color:#333}
  .field-input{left:588px;width:214px;height:28px;border:1px solid var(--field-border);padding-left:16px;font-size:12px;letter-spacing:1px;line-height:26px;color:#111}
  .twofa{left:406px;top:505px;font-size:15px;color:#333}
  .radio{top:507px;width:13px;height:13px;border-radius:50%;border:1px solid #888}
  .radio.on::after{content:"";position:absolute;left:2px;top:2px;width:7px;height:7px;border-radius:50%;background:var(--brand)}
  .radio-label{top:505px;font-size:15px;color:#333}

  /* footer */
  .site-footer{left:0;top:572px;width:1200px;height:331px;background:var(--brand);color:#fff}
  .foot-brand{left:111px;top:44px;width:140px;font-size:11px;letter-spacing:5px;line-height:20px;text-transform:uppercase}
  .foot-divider{left:256px;top:40px;width:1px;height:70px;background:#fff}
  .foot-dot{left:270px;top:52px;width:14px;height:14px;border-radius:50%;background:#fff}
  .copyright{left:110px;top:124px;font-size:11px;line-height:14px}
  .foot-heading{top:42px;font-size:22px;font-weight:700}
  .foot-links{top:80px;list-style:none;font-size:12px;line-height:15px}
  .social{top:80px;width:27px;height:27px;border-radius:50%;background:#e8f5fb}
  .tagline-art{left:504px;top:206px;width:575px;height:82px;background:linear-gradient(90deg,#1aa3d8,#33b2e2,#1aa3d8);border-radius:4px}
</style>
</head>
<body>
<div class="stage">
  <div class="page">
    <header>
      <div class="abs brand-name">Northway Value Bureau</div>
      <div class="abs brand-divider"></div>
      <div class="abs brand-dot"></div>
      <nav class="abs main-nav">Home · About · Trading &nbsp;· Support &nbsp;· Account (Demo) - Logout</nav>
      <div class="abs login-field" style="left:694px">Email<span class="hint">?</span></div>
      <div class="abs login-field" style="left:834px">Password<span class="hint">?</span></div>
      <div class="abs btn btn-login">Log In</div>
      <div class="abs btn btn-signup">Sign Up</div>
    </header>

    <section class="abs ticker">
      <div class="abs coin-mark" role="img" aria-label="Currency symbol"></div>
      <div class="abs tick" style="left:282px">Current Price<b>$444.13</b></div>
      <div class="abs tick-rule" style="left:370px"></div>
      <div class="abs tick" style="left:396px">Daily Change<b>-9.54 <small>▾2.10%</small></b></div>
      <div class="abs tick-rule" style="left:495px"></div>
      <div class="abs tick" style="left:521px">Day's Range<b>$440.00 - $457.30</b></div>
      <div class="abs tick-rule" style="left:663px"></div>
      <div class="abs tick" style="left:689px">Today's Open<b>$453.57</b></div>
      <div class="abs tick-rule" style="left:781px"></div>
      <div class="abs tick" style="left:807px">24h Volume<b>7194 BTC</b></div>
    </section>

    <div class="abs title-band"><h1 class="abs page-title">Account Profile</h1></div>

    <ul class="abs side-menu">
      <li>Profile</li>
      <li>Transfers<span class="expand">+</span></li>
      <li>Reports</li>
      <li>Security</li>
      <li>API Key</li>
      <li>Affiliates</li>
    </ul>

    <h2 class="abs section-title">Security</h2>
    <h3 class="abs form-heading">Change Password</h3>
    <div class="abs field-label" style="top:375px">Current Password:</div>
    <div class="abs field-input" style="top:369px">●●●●●●●●●●</div>
    <div class="abs field-label" style="top:415px">New Password:</div>
    <div class="abs field-input" style="top:409px">●●●●●●●●●●</div>
    <div class="abs field-label" style="top:455px">Confirm New Password:</div>
    <div class="abs field-input" style="top:449px">●●●●●●●●●●</div>
    <div class="abs twofa">Two-factor Authentication (SMS):</div>
    <div class="abs radio" style="left:652px"></div>
    <div class="abs radio-label" style="left:676px">Enable</div>
    <div class="abs radio on" style="left:750px"></div>
    <div class="abs radio-label" style="left:774px">Disable</div>

    <footer class="abs site-footer">
      <div class="abs foot-brand">Northway Value Bureau</div>
      <div class="abs foot-divider"></div>
      <div class="abs foot-dot"></div>
      <div class="abs copyright">© 2014 Northway Value Bureau.<br>All rights reserved</div>

      <h4 class="abs foot-heading" style="left:450px">ABOUT US</h4>
      <ul class="abs foot-links" style="left:450px">
        <li>Rulebook</li><li>Trading Fees</li><li>Partners</li><li>Security</li>
        <li>Terms of Service</li><li>Privacy Policy</li><li>Latest News</li>
      </ul>
      <h4 class="abs foot-heading" style="left:706px">SUPPORT</h4>
      <ul class="abs foot-links" style="left:706px">
        <li>What is Bitcoin?</li><li>How to buy a bitcoin?</li><li>How to sell a bitcoin?</li>
      </ul>
      <h4 class="abs foot-heading" style="left:936px">FOLLOW NVB</h4>
      <div class="abs social" style="left:936px" role="img" aria-label="Social link"></div>
      <div class="abs social" style="left:976px" role="img" aria-label="Social link"></div>
      <div class="abs social" style="left:1017px" role="img" aria-label="Social link"></div>
      <div class="abs social" style="left:1057px" role="img" aria-label="Social link"></div>

      <div class="abs tagline-art" role="img" aria-label="Hand-lettered brand tagline"></div>
    </footer>
  </div>
</div>
</body>
</html>
```